Brekwell Automotive needs a catchy banner design

We need a design for a banner to be displayed on the fence in the outfield of a baseball stadium to show off our company and have people interested in what we do. We need something catchy that's going to attract people to look over at our banner.
We are a
Complete Automotive Service Company
Tires - Service - Repair - Diesel
We are in a Town called Ashford-Linden
(555)314-2609 we would like the phone number to be a descent size so when you are in the stands you can read it.
I have attached what we came up with but like I said we need it to pop more and make the viewer that's looking at it want to look us up.
The Banner size is 24ft long and 10ft tall

```html
<!DOCTYPE html>
<html lang="en">
<head>
<meta charset="utf-8">
<title>Brekwell Automotive – Outfield Banner</title>
<link rel="stylesheet" href="https://fonts.googleapis.com/css2?family=Arimo:wght@400;700&family=Nunito:wght@300;400;800;900&display=swap">
<style>
  :root {
    --page-bg: #f4f4f4;
    --banner-black: #000000;
    --car-dark: #0b0b0c;
    --car-mid: #26272a;
    --brand-blue: #1565d8;
    --tab-blue: #0d4fb0;
    --text-white: #ffffff;
  }
  * { margin: 0; padding: 0; box-sizing: border-box; }
  html, body {
    width: 1200px;
    height: 1200px;
    overflow: hidden;
    background: var(--page-bg);
  }
  .banner {
    position: absolute;
    left: 40px;
    top: 367px;
    width: 1120px;
    height: 466px;
    background: var(--banner-black);
    overflow: hidden;
    box-shadow: 0 18px 24px -12px rgba(0,0,0,0.45);
  }
  .car-photo {
    position: absolute;
    left: 0;
    top: 0;
    width: 300px;
    height: 466px;
    z-index: 2;
    background: radial-gradient(ellipse 70% 45% at 62% 40%, var(--car-mid) 0%, var(--car-dark) 55%, var(--banner-black) 100%);
  }
  .brand-name {
    position: absolute;
    left: 306px;
    top: 70px;
    width: 226px;
    z-index: 3;
    font-family: "Arimo", Arial, sans-serif;
    font-weight: 700;
    font-size: 36px;
    line-height: 1.1;
    color: var(--brand-blue);
    text-align: center;
  }
  .headline {
    position: absolute;
    left: 548px;
    top: 36px;
    font-family: "Arimo", Arial, sans-serif;
    font-weight: 400;
    font-size: 56px;
    line-height: 1.12;
    color: var(--text-white);
    white-space: nowrap;
  }
  .headline strong { font-weight: 700; }
  .phone-band {
    position: absolute;
    left: 291px;
    top: 198px;
    width: 829px;
    height: 97px;
    background: var(--brand-blue);
    z-index: 1;
  }
  .phone-number {
    position: absolute;
    left: 330px;
    width: 720px;
    top: 196px;
    z-index: 3;
    font-family: "Nunito", Arial, sans-serif;
    font-weight: 900;
    font-size: 92px;
    line-height: 100px;
    color: var(--text-white);
    text-align: center;
    letter-spacing: -1px;
  }
  .services-tab {
    position: absolute;
    left: 451px;
    top: 295px;
    width: 481px;
    height: 36px;
    z-index: 3;
  }
  .services-tab svg { position: absolute; inset: 0; }
  .services-tab span {
    position: relative;
    display: block;
    text-align: center;
    font-family: "Nunito", Arial, sans-serif;
    font-weight: 400;
    font-size: 30px;
    line-height: 34px;
    color: var(--text-white);
    white-space: nowrap;
  }
  .town {
    position: absolute;
    left: 372px;
    width: 636px;
    top: 366px;
    font-family: "Nunito", Arial, sans-serif;
    font-weight: 800;
    font-size: 42px;
    color: var(--text-white);
    text-align: center;
  }
</style>
</head>
<body>
  <section class="banner">
    <div class="car-photo" role="img" aria-label="Dark sports car front with glowing headlights on black background"></div>
    <div class="brand-name">Brekwell Automotive</div>
    <h1 class="headline">From <strong>Oil Chages</strong> to<br><strong>Custom Builds</strong></h1>
    <div class="phone-band"></div>
    <div class="phone-number">(555)314-2609</div>
    <div class="services-tab">
      <svg width="481" height="36" viewBox="0 0 481 36" aria-hidden="true">
        <path d="M0 0 H481 L467 30 Q464 36 457 36 H24 Q17 36 14 30 Z" fill="var(--tab-blue)"/>
      </svg>
      <span>Tires - Service - Repair - Diesel</span>
    </div>
    <p class="town">Ashford-Linden</p>
  </section>
</body>
</html>
```